Corvane Lending Partners. Professional and Established Company

A full service finance company specializing in obtaining capital for small business. Business Lending advisor, helping small business owners access the capital they need to launch, grow, or sustain their business. Many of our programs offer flexible guidelines to overcome common obstacles such as credit score, credit history, and time in business, financials, and industry type. Our streamlined funding process makes getting a business loan, business line of credit, stated income commercial real estate loan, a smooth and stress free experience.SOME OF THE MOST COMMON NEEDS FOR BUSINESS CAPITAL:• Working Capital• Debt Consolidations (loans, merchant cash advances, etc.)• Payroll• Operating Expenses• Inventory• Equipment Financing• Commercial Real Estate (Purchase, Fix & Flip, Rehab, Renovations)• Business Acquisitions• Business ExpansionWe like the websites:www.quillmorecf.com they are in the same industry and provide the same servicesWe are wanting to be able to update when we do press releases and such using Word Press. Our look should be very professional and we will be adding Our Team Professional Bios and Headshots.

Industry/Entity Type

Finance

Number of Pages Required

5+ page

Font styles to use
Serif
Sans Serif

Requirements
Must have
• We want to copy quillmorecf.com
• We need:
• Home Page
• About Us
• Loan Programs
• Loan Criteria
• News
• Apply Now
• Contact
Nice to have
• See quillmorecf.com
Should not have
• Need professional design. Nothing bright or abstract

```html
<!DOCTYPE html>
<html lang="en">
<head>
<meta charset="utf-8">
<title>Corvane Lending Partners</title>
<link rel="stylesheet" href="https://fonts.googleapis.com/css2?family=Libre+Baskerville:wght@400&family=Open+Sans:wght@400;600&display=swap">
<style>
:root{
  --blue:#1f5fb0;
  --blue-dark:#174a8c;
  --team:#2563b5;
  --ink:#1c2a3a;
  --text:#6d6d6d;
  --panel:#f3f3f3;
  --footer:#1f1f21;
  --white:#ffffff;
}
*{box-sizing:border-box;margin:0;padding:0}
html,body{width:1200px;height:4027px;overflow:hidden;background:var(--white)}
body{font-family:"Open Sans",Arial,sans-serif;color:var(--text);position:relative}
.serif{font-family:"Libre Baskerville",Georgia,serif}

/* header */
.site-header{position:absolute;top:0;left:0;width:1200px;height:121px;border-top:5px solid var(--blue);background:var(--white)}
.brand{position:absolute;left:113px;top:30px;width:260px;font-family:"Libre Baskerville",Georgia,serif;font-size:27px;line-height:31px;color:var(--blue)}
.contact-bar{position:absolute;right:113px;top:30px;display:flex;gap:34px;font-family:"Libre Baskerville",Georgia,serif;font-size:13px;color:#777;align-items:center}
.contact-bar span{display:flex;align-items:center;gap:8px}
.main-nav{position:absolute;left:408px;top:80px;display:flex;gap:38px;font-family:"Libre Baskerville",Georgia,serif;font-size:12.5px;color:#444;text-transform:uppercase}
.main-nav .active{color:var(--blue)}

/* hero */
.hero{position:absolute;top:121px;left:0;width:1200px;height:582px;background:linear-gradient(100deg,#3b3b40 0%,#5a5756 35%,#2a2c31 70%,#1c1e22 100%)}
.hero-photo{position:absolute;inset:0}
.hero-copy{position:absolute;left:655px;top:172px;width:410px;color:var(--white)}
.hero-title{font-family:"Libre Baskerville",Georgia,serif;font-size:44px;line-height:52px;padding-bottom:14px;border-bottom:3px solid var(--white);margin-bottom:22px}
.hero-copy p{font-size:13px;line-height:22px}
.btn-solid{display:inline-block;margin-top:26px;background:var(--blue);color:var(--white);font-family:"Libre Baskerville",Georgia,serif;font-size:14px;padding:14px 30px}
.arrow{position:absolute;top:271px;width:36px;height:36px}

/* headings */
.section-title{font-family:"Libre Baskerville",Georgia,serif;color:var(--blue);text-transform:uppercase;font-size:32px;letter-spacing:.5px}
.title-rule{display:block;height:2px;background:var(--blue);margin-top:6px}
.center{text-align:center}
.center .section-title{display:inline-block}

.welcome{position:absolute;top:703px;left:0;width:1200px;height:250px}
.welcome .heading{position:absolute;top:40px;left:0;width:100%;text-align:center}
.welcome p{position:absolute;top:120px;left:236px;width:728px;font-size:12.5px;line-height:27px;text-align:center}

/* split rows */
.split{position:absolute;left:0;width:1200px;height:369px;display:flex}
.split .panel{width:601px;height:100%;background:var(--panel);position:relative}
.split .photo{width:599px;height:100%}
.panel .section-title{font-size:30px}
.panel .heading{position:absolute;top:50px;display:inline-block}
.panel p{position:absolute;top:125px;width:410px;font-size:12.5px;line-height:26px}
.btn-outline{position:absolute;top:277px;border:2px solid var(--blue);color:var(--blue);font-family:"Libre Baskerville",Georgia,serif;font-size:13px;padding:9px 20px}

/* services */
.services-intro{position:absolute;top:1691px;left:0;width:1200px;height:194px;text-align:center}
.services-intro .heading{margin-top:48px;display:inline-block}
.services-intro p{width:740px;margin:20px auto 0;font-size:12.5px;line-height:26px}
.service-grid{position:absolute;top:1885px;left:0;width:1200px;display:grid;grid-template-columns:400px 400px 400px}
.service-card{height:446px}
.service-photo{height:271px}
.service-card h3{font-family:"Libre Baskerville",Georgia,serif;font-weight:400;font-size:15px;color:var(--ink);text-transform:uppercase;text-align:center;margin-top:20px}
.service-card p{width:330px;margin:16px auto 0;text-align:center;font-size:12.5px;line-height:24px}

/* team */
.team{position:absolute;top:3225px;left:0;width:1200px;height:496px;background:linear-gradient(135deg,#2a6bc0,#1f58a8);color:var(--white);text-align:center}
.team .section-title{color:var(--white)}
.team .title-rule{background:var(--white)}
.team .heading{display:inline-block;margin-top:38px}
.team-intro{font-size:13px;margin-top:10px}
.member{position:absolute;top:155px;width:320px;text-align:center}
.headshot{width:150px;height:150px;border-radius:50%;border:4px solid var(--white);margin:0 auto;background:linear-gradient(#d9d2cb,#8c7a6a)}
.member h4{font-family:"Libre Baskerville",Georgia,serif;font-weight:400;font-size:15px;margin-top:26px;text-transform:uppercase}
.member p{font-size:12.5px;line-height:24px;margin-top:10px;width:240px;margin-left:auto;margin-right:auto}
.mini-social{display:flex;justify-content:center;gap:8px;margin-top:16px}
.mini-social i{width:30px;height:30px;border:1.5px solid var(--white);border-radius:50%}

/* footer */
.site-footer{position:absolute;top:3721px;left:0;width:1200px;height:306px;background:var(--footer);text-align:center;color:#cfcfcf}
.footer-brand{position:absolute;top:42px;left:0;width:100%;font-family:"Libre Baskerville",Georgia,serif;font-size:34px;color:#3d7bd0}
.footer-rule{position:absolute;top:145px;left:113px;width:974px;height:1px;background:#3a3a3d}
.footer-social{position:absolute;top:164px;left:0;width:100%;display:flex;justify-content:center;gap:14px}
.footer-social i{width:60px;height:60px;border:1.5px solid #bdbdbd;border-radius:50%;display:flex;align-items:center;justify-content:center}
.copyright{position:absolute;top:258px;width:100%;font-size:12px}
</style>
</head>
<body>

<header class="site-header">
  <div class="brand">Corvane Lending Partners</div>
  <div class="contact-bar">
    <span><svg width="14" height="14" viewBox="0 0 24 24"><path fill="#1f5fb0" d="M6.6 10.8a15 15 0 0 0 6.6 6.6l2.2-2.2c.3-.3.7-.4 1-.2 1.1.4 2.3.6 3.6.6.6 0 1 .4 1 1V20c0 .6-.4 1-1 1A17 17 0 0 1 3 4c0-.6.4-1 1-1h3.5c.6 0 1 .4 1 1 0 1.3.2 2.5.6 3.6.1.3 0 .7-.2 1z"/></svg>Call US : 800-555-0148</span>
    <span><svg width="15" height="12" viewBox="0 0 24 18"><rect x="1" y="1" width="22" height="16" fill="#1f5fb0"/><path d="M1 1l11 9 11-9" stroke="#fff" stroke-width="2" fill="none"/></svg>Email : info@corvanelending.com</span>
  </div>
  <nav class="main-nav">
    <span class="active">Home</span><span>About Us</span><span>Loan Programs</span><span>Loan Criteria</span><span>News</span><span>Apply Now</span><span>Contact</span>
  </nav>
</header>

<section class="hero">
  <div class="hero-photo" role="img" aria-label="Businessman reviewing financial charts on a laptop in a dim office"></div>
  <svg class="arrow" style="left:62px" viewBox="0 0 36 36"><circle cx="18" cy="18" r="16" fill="none" stroke="#fff" stroke-width="2"/><path d="M21 11l-7 7 7 7" stroke="#fff" stroke-width="2.5" fill="none"/></svg>
  <svg class="arrow" style="left:1096px" viewBox="0 0 36 36"><circle cx="18" cy="18" r="16" fill="none" stroke="#fff" stroke-width="2"/><path d="M15 11l7 7-7 7" stroke="#fff" stroke-width="2.5" fill="none"/></svg>
  <div class="hero-copy">
    <div class="hero-title">CORVANE</div>
    <p>Flexible business capital for owners who need to launch, grow or sustain their company, with guidelines built around real credit and time in business.</p>
    <span class="btn-solid">READ MORE</span>
  </div>
</section>

<section class="welcome">
  <div class="heading"><span class="section-title">Welcome to Corvane</span><span class="title-rule" style="width:300px;margin:6px auto 0"></span></div>
  <p>Corvane Lending Partners is a full service finance company specializing in obtaining capital for small business. We help owners access the funding they need through a streamlined process that keeps every loan, line of credit and real estate deal smooth.</p>
</section>

<section class="split" style="top:953px">
  <div class="panel">
    <div class="heading" style="left:113px"><span class="section-title">Loan Programs</span><span class="title-rule"></span></div>
    <p style="left:113px">Our programs offer flexible guidelines for business loans, lines of credit and stated income commercial real estate loans. We match each owner with capital that fits the stage and the needs of their company, from a first launch to steady growth.</p>
    <span class="btn-outline" style="left:113px">READ MORE</span>
  </div>
  <div class="photo" role="img" aria-label="Hands typing on a laptop showing financial dashboards" style="background:linear-gradient(135deg,#c8ccd2,#4e5866 60%,#2c333d)"></div>
</section>

<section class="split" style="top:1322px">
  <div class="photo" role="img" aria-label="Hand using a calculator over printed financial reports" style="background:linear-gradient(135deg,#e6e1da,#9a8f86 55%,#3d3a3a)"></div>
  <div class="panel">
    <div class="heading" style="left:78px"><span class="section-title">Loan Criteria</span><span class="title-rule"></span></div>
    <p style="left:78px">We look past common obstacles such as credit score, credit history, time in business, financials and industry type. Many owners who were turned away by banks qualify with us, and our advisors guide you through each step of the process.</p>
    <span class="btn-outline" style="left:78px">READ MORE</span>
  </div>
</section>

<section class="services-intro">
  <div class="heading"><span class="section-title">Our Services</span><span class="title-rule"></span></div>
  <p>Some of the most common needs for business capital, each supported by a funding path designed for small business owners and the way they actually operate.</p>
</section>

<section class="service-grid">
  <article class="service-card"><div class="service-photo" role="img" aria-label="Team meeting around an office table" style="background:linear-gradient(135deg,#eef0f2,#aeb6c0)"></div><h3>Working Capital</h3><p>Keep daily operations moving with fast access to cash for the gaps between revenue cycles.</p></article>
  <article class="service-card"><div class="service-photo" role="img" aria-label="Debt consolidation loan form on a laptop with a payment card" style="background:linear-gradient(135deg,#8c8a88,#4b4644)"></div><h3>Debt Consolidations</h3><p>Combine loans and merchant cash advances into one payment that is easier to manage each month.</p></article>
  <article class="service-card"><div class="service-photo" role="img" aria-label="Hand writing on papers beside a calculator" style="background:linear-gradient(135deg,#d8d3cd,#7e766e)"></div><h3>Payroll</h3><p>Pay your team on time, every time, even when receivables arrive later than you planned.</p></article>
  <article class="service-card"><div class="service-photo" role="img" aria-label="Hands reviewing documents on a desk" style="background:linear-gradient(135deg,#e4ddd3,#9b8873)"></div><h3>Operating Expenses</h3><p>Cover rent, utilities and supplies so the business keeps running while you focus on growth.</p></article>
  <article class="service-card"><div class="service-photo" role="img" aria-label="Person holding a tablet in a warehouse" style="background:linear-gradient(135deg,#8a8f96,#3f454d)"></div><h3>Inventory</h3><p>Stock up ahead of busy seasons and take advantage of supplier discounts with ready funding.</p></article>
  <article class="service-card"><div class="service-photo" role="img" aria-label="Phone and notebook on an office desk" style="background:linear-gradient(135deg,#c9a57a,#5e4a36)"></div><h3>Equipment Financing</h3><p>Buy or upgrade the machines, vehicles and tools your company relies on without draining cash.</p></article>
  <article class="service-card"><div class="service-photo" role="img" aria-label="Businessman presenting a model of city buildings" style="background:linear-gradient(135deg,#e9edf2,#7d8fa6 60%,#2f3b4c)"></div><h3>Commercial Real Estate</h3><p>Purchase, fix and flip, rehab or renovate property with stated income commercial loans.</p></article>
  <article class="service-card"><div class="service-photo" role="img" aria-label="Business partners shaking hands over a conference table" style="background:linear-gradient(135deg,#b7b0a6,#5d544b)"></div><h3>Business Acquisitions</h3><p>Fund the purchase of an existing company and step into an established customer base.</p></article>
  <article class="service-card"><div class="service-photo" role="img" aria-label="Businessman standing on a mountain top at sunrise" style="background:linear-gradient(180deg,#e8dcc3,#8d8a80 60%,#4a4a48)"></div><h3>Business Expansion</h3><p>Open new locations, hire staff and reach new markets with capital sized to your plans.</p></article>
</section>

<section class="team">
  <div class="heading"><span class="section-title">Our Team</span><span class="title-rule"></span></div>
  <p class="team-intro">Experienced lending advisors who help small business owners find the capital they need.</p>
  <div class="member" style="left:125px"><div class="headshot" role="img" aria-label="Headshot of a team member"></div><h4>Dana Whitfield</h4><p>Senior advisor focused on working capital and payroll funding.</p><div class="mini-social"><i></i><i></i></div></div>
  <div class="member" style="left:441px"><div class="headshot" role="img" aria-label="Headshot of a team member"></div><h4>Priya Halvorsen</h4><p>Lending specialist for equipment financing and inventory lines.</p><div class="mini-social"><i></i><i></i></div></div>
  <div class="member" style="left:758px"><div class="headshot" role="img" aria-label="Headshot of a team member"></div><h4>Marcus Ellery</h4><p>Commercial real estate and acquisition loan advisor.</p><div class="mini-social"><i></i><i></i></div></div>
</section>

<footer class="site-footer">
  <div class="footer-brand">Corvane Lending Partners</div>
  <div class="footer-rule"></div>
  <div class="footer-social">
    <i></i><i></i><i></i><i></i><i></i>
    <i><svg width="22" height="16" viewBox="0 0 24 18"><rect x="1" y="1" width="22" height="16" fill="none" stroke="#cfcfcf" stroke-width="1.6"/><path d="M1 1l11 9 11-9" stroke="#cfcfcf" stroke-width="1.6" fill="none"/></svg></i>
  </div>
  <div class="copyright">© Copyrights 2018 - Corvane All Rights Reserved.</div>
</footer>

</body>
</html>
```